New B2C website design to help dads be better dads

DadHarbor is a website to help dads be the “best dad you can be.”

We require our website to be designed into a PSD format, no coding necessary.

The general concept is a two-page design. The first page is the login page, the second page is the home page. Once at the home page, rather than navigating to and from different pages, the user will push and pull through different visual and functional layers of the hierarchy. In theory, this should add to the user experience by having a visual anchor of where they are (through layered pagination) as well as improving loading times since the new information should only be a delta in data load versus a brand new page load.

The general look-and-feel we are going for is clean, simple, minimal. This means that the winning design will show us a good eye for web-optimized typography, good use of white (negative) space, and good use of a visually pleasing grid.

We require a total of 6 page "views" plus the landing page. We note that many of the views are similar to one another.
Landing page
Milestone view
Task view
Content view, articles
Content view, products
Search view
What's new view

Please review all of the additional information provided as well as the attachments for examples.

We provide the following websites as good references for:

Typography:
http://example-kelvorn.com/journal/

Use of white space:
http://www.trenvaskit.com/
http://moldrefin.com/

Example for “scrolling” page concept as well as good balance of color, typography, and white space:
http://www.qorbitalmeet.eu/

Please contact us with questions so that we can guide your design effort.
Updates

Hello designers,

The following information is added to help guide the design process:

1.  For the text dialogue below the landing page, please assume the following word count:
"why are we making dad harbor?": 250 words
"who are we?" 200 words
"what's the deal with the penguin logo?" 300 words

For the social media links, please see http://www.gravelplumbs.com/
Notice the floating "social" bar that is always to the right.  This is the concept we are going for, please try to implement this as you see fit. 

Target Market(s)

Fathers of young children ages 0-6 years old.

Industry/Entity Type

Product

Font styles to use
Sans Serif

Requirements
Must have
• Clean lines, minimal design concept

Incorporation of our logo (see attached document)

Header content is static for all views after landing page, see example

This page WILL be responsive, please keep that in mind when designing
The timeline bar should be to the left, with the timeline bar’s “milestones” also being responsive.

Designer is free to suggest font types, but any fonts used must be royalty-free and web-optimized. We request a minimum number of font types as well as fonts that load relatively fast. We reinforce that visually appealing typography is a significant factor in the winning design choice.

While we are not expecting the winning design to include code, please keep in mind that the final implementation needs to be optimized for desktop, tablet, and mobile platforms.

If you are using stock photography that is not generated by you, please provide where/how we can obtain imagery, as well as price.

All custom graphics must be available in original formats; Photoshop/GIMP layered files for layout design, and vector formats for logos, icons and other graphical elements.

Please incorporate “Blue” into design elements as you see fit, as the RGB 67 74 169 Blue is the primary color used in our brand. The complement to this blue is 255 202 0, a brownish orange. Feel free to use this color as well, although please keep it to a lesser amount.

Background color is your choice, do not feel the need to use the grey.
Should not have
• Excessive graphical content such that it affects loading times

Excessive use of too many font types such that it affects loading times

```html
<!DOCTYPE html>
<html lang="en">
<head>
<meta charset="utf-8">
<title>DadHarbor – Milestone view</title>
<link rel="stylesheet" href="https://fonts.googleapis.com/css2?family=Montserrat:wght@400;500;600&family=Hind:wght@300;400&display=swap">
<style>
  :root {
    --brand-blue: #434aa9;
    --star-gold: #ffca00;
    --ink: #2b2b2b;
    --ink-soft: #555;
    --panel-bg: #f7f7f7;
    --line: #c9cbe6;
    --page-bg: #ffffff;
  }
  * { box-sizing: border-box; margin: 0; padding: 0; }
  html, body { width: 1200px; height: 1068px; overflow: hidden; background: var(--page-bg); }
  body { position: relative; font-family: "Hind", sans-serif; color: var(--ink); }

  .abs { position: absolute; }

  /* Header */
  .brand { left: 185px; top: 40px; display: flex; align-items: center; gap: 8px; }
  .brand-dot { width: 14px; height: 14px; border-radius: 50%; background: var(--brand-blue); }
  .brand-name { font-family: "Montserrat", sans-serif; font-weight: 600; font-size: 16px; color: var(--brand-blue); letter-spacing: 0.5px; }
  .welcome { left: 329px; top: 18px; font-family: "Montserrat", sans-serif; font-weight: 500; font-size: 21px; color: #444; letter-spacing: 0.4px; }
  .score { left: 329px; top: 82px; font-family: "Montserrat", sans-serif; font-weight: 500; font-size: 12.5px; color: #333; }
  .search { left: 542px; top: 71px; width: 286px; height: 36px; border: 1px solid #e2e2e2; background: #f8f8f8; }
  .search-btn { position: absolute; right: 4px; top: 4px; width: 83px; height: 26px; background: var(--brand-blue); color: #fff;
    font-family: "Montserrat", sans-serif; font-size: 12.5px; font-weight: 500; display: flex; align-items: center; justify-content: center; }
  .account-links { left: 847px; top: 78px; font-family: "Montserrat", sans-serif; font-size: 16.5px; color: var(--brand-blue); }

  /* Panel */
  .panel-frame { left: 0; top: 0; }
  .timeline-node { width: 24px; height: 24px; }
  .timeline-label { font-family: "Montserrat", sans-serif; font-size: 10px; width: 70px; text-align: center; }
  .timeline-label.current { color: var(--brand-blue); }
  .milestone-title { left: 252px; top: 200px; font-family: "Montserrat", sans-serif; font-size: 13px; color: var(--brand-blue); }

  .task-list { left: 253px; top: 278px; width: 197px; height: 259px; border: 1px solid var(--line); background: #fff; list-style: none; padding-top: 13px; }
  .task { display: flex; align-items: center; height: 30.2px; padding-left: 10px; font-family: "Montserrat", sans-serif; font-size: 11px; color: #555; }
  .task-box { width: 11px; height: 11px; border: 1px solid var(--brand-blue); margin-right: 12px; display: flex; align-items: center; justify-content: center; }

  .card { width: 197px; }
  .card-media { width: 196px; height: 119px; }
  .card-type { margin-top: 8px; font-family: "Montserrat", sans-serif; font-weight: 600; font-size: 12.5px; color: var(--brand-blue); letter-spacing: 0.4px; }
  .card-meta { margin-top: 6px; display: flex; align-items: center; justify-content: space-between; }
  .stars { display: flex; gap: 2px; }
  .ratings { font-size: 13px; font-weight: 300; color: var(--brand-blue); }
  .card-text { margin-top: 5px; font-size: 11.5px; font-weight: 300; line-height: 21.3px; color: #222; text-align: justify; }

  .sort { left: 911px; top: 242px; font-size: 13px; }
  .sort-title { color: var(--brand-blue); font-weight: 300; margin-bottom: 12px; }
  .sort-option { font-size: 11.5px; color: #111; height: 30.3px; font-weight: 300; }

  .more-btn { left: 469px; top: 901px; width: 335px; height: 57px; background: var(--brand-blue); color: #fff;
    font-family: "Montserrat", sans-serif; font-weight: 600; font-size: 15px; letter-spacing: 0.5px; text-align: center; padding-top: 19px; }
  .more-chevron { left: 622px; top: 946px; }

  .footer { left: 0; top: 998px; width: 1200px; height: 70px; background: var(--brand-blue); color: #fff; font-size: 13px; font-weight: 300;
    display: flex; align-items: center; justify-content: center; }
</style>
</head>
<body>
  <svg width="0" height="0" class="abs" aria-hidden="true">
    <defs>
      <symbol id="star" viewBox="0 0 20 20">
        <polygon points="10,1 12.6,7.2 19.4,7.6 14.2,12 15.9,18.7 10,15 4.1,18.7 5.8,12 0.6,7.6 7.4,7.2" fill="var(--star-gold)" stroke="#e0a800" stroke-width="0.6"/>
      </symbol>
    </defs>
  </svg>

  <!-- Header -->
  <div class="abs brand"><span class="brand-dot"></span><span class="brand-name">DADHARBOR</span></div>
  <h1 class="abs welcome">Welcome Tobin ,What would you like to do today ?</h1>
  <p class="abs score">Super Dad Score: 10,500</p>
  <div class="abs search"><span class="search-btn">Search</span></div>
  <nav class="abs account-links">My Account |&nbsp; Logout</nav>

  <!-- Panel frame -->
  <svg class="abs panel-frame" width="1200" height="1000" aria-hidden="true">
    <path d="M234 256 V958 H1026 V164.5 H172.5 V256 Z" fill="var(--panel-bg)"/>
    <path d="M234 256 V958 H1026 V164.5 H172.5 V256 H234" fill="none" stroke="var(--line)" stroke-width="1"/>
    <line x1="203" y1="267" x2="203" y2="843" stroke="#dcdcdc" stroke-width="1"/>
  </svg>

  <!-- Timeline -->
  <svg class="abs timeline-node" style="left:190px;top:198px" viewBox="0 0 24 24" aria-hidden="true">
    <circle cx="12" cy="12" r="10.5" fill="#fff" stroke="var(--brand-blue)" stroke-width="2"/>
    <path d="M12 7v10M7 12h10" stroke="var(--brand-blue)" stroke-width="1.6"/>
  </svg>
  <span class="abs timeline-label current" style="left:167px;top:227px">-3 Months</span>
  <svg class="abs timeline-node" style="left:190px;top:842px" viewBox="0 0 24 24" aria-hidden="true">
    <circle cx="12" cy="12" r="10.5" fill="#fff" stroke="var(--brand-blue)" stroke-width="2"/>
    <path d="M12 7v10M7 12h10" stroke="var(--brand-blue)" stroke-width="1.6"/>
  </svg>
  <span class="abs timeline-label" style="left:167px;top:871px">0 Months</span>

  <h2 class="abs milestone-title">Prepare for the baby arrival</h2>

  <!-- Tasks -->
  <ul class="abs task-list">
    <li class="task"><span class="task-box"></span>Buy a crib</li>
    <li class="task"><span class="task-box"></span>Assemble the crib</li>
    <li class="task"><span class="task-box"></span>Buy a stroller</li>
    <li class="task"><span class="task-box"><svg width="9" height="9" viewBox="0 0 9 9"><path d="M1 4.5l2.3 2.4L8 1.5" fill="none" stroke="#2a9d3a" stroke-width="1.5"/></svg></span>Buy a carseat</li>
    <li class="task"><span class="task-box"></span>Install a carseat</li>
    <li class="task"><span class="task-box"></span>Learn to change a diaper</li>
    <li class="task"><span class="task-box"></span>Learn to hold a baby</li>
    <li class="task"><span class="task-box"></span>Set a feeding schedule</li>
  </ul>

  <!-- Cards -->
  <article class="abs card" style="left:466px;top:278px">
    <div class="card-media" role="img" aria-label="Photo of a father holding his smiling toddler outdoors" style="background:linear-gradient(135deg,#6f7f4a,#b9773f 55%,#8a4f2a)"></div>
    <div class="card-type">ARTICLE</div>
    <div class="card-meta"><span class="stars"><svg width="18" height="18"><use href="#star"/></svg><svg width="18" height="18"><use href="#star"/></svg><svg width="18" height="18"><use href="#star"/></svg><svg width="18" height="18"><use href="#star"/></svg><svg width="18" height="18"><use href="#star"/></svg></span><span class="ratings">1328 Ratings</span></div>
    <p class="card-text">I went out to buy my first car seat and had to earn my PhD in car seats, Newtonian physics, and anti-stain technology…</p>
  </article>
  <article class="abs card" style="left:680px;top:278px">
    <div class="card-media" role="img" aria-label="Product photo of an orange and black baby stroller" style="background:radial-gradient(circle at 50% 45%,#d9733f 0,#5a4a44 28%,#ffffff 46%)"></div>
    <div class="card-type">PRODUCT</div>
    <div class="card-meta"><span class="stars"><svg width="18" height="18"><use href="#star"/></svg><svg width="18" height="18"><use href="#star"/></svg><svg width="18" height="18"><use href="#star"/></svg><svg width="18" height="18"><use href="#star"/></svg><svg width="18" height="18"><use href="#star"/></svg></span><span class="ratings">1328 Ratings</span></div>
    <p class="card-text">I went out to buy my first car seat and had to earn my PhD in car seats, Newtonian physics, and anti-stain technology…</p>
  </article>
  <article class="abs card" style="left:466px;top:536px">
    <div class="card-media" role="img" aria-label="Photo of a child resting on a parent's shoulder" style="background:linear-gradient(135deg,#c9b27a,#d7a48c 45%,#4d6f8a 80%)"></div>
    <div class="card-type">ARTICLE</div>
    <div class="card-meta"><span class="stars"><svg width="18" height="18"><use href="#star"/></svg><svg width="18" height="18"><use href="#star"/></svg><svg width="18" height="18"><use href="#star"/></svg><svg width="18" height="18"><use href="#star"/></svg><svg width="18" height="18"><use href="#star"/></svg></span><span class="ratings">1328 Ratings</span></div>
    <p class="card-text">I went out to buy my first car seat and had to earn my PhD in car seats, Newtonian physics, and anti-stain technology…</p>
  </article>
  <article class="abs card" style="left:680px;top:536px">
    <div class="card-media" role="img" aria-label="Product photo of a baby on a colourful play gym" style="background:linear-gradient(90deg,#8ec4df,#e8c9a8 35%,#7fb7d9 62%,#ffffff 66%)"></div>
    <div class="card-type">PRODUCT</div>
    <div class="card-meta"><span class="stars"><svg width="18" height="18"><use href="#star"/></svg><svg width="18" height="18"><use href="#star"/></svg><svg width="18" height="18"><use href="#star"/></svg><svg width="18" height="18"><use href="#star"/></svg><svg width="18" height="18"><use href="#star"/></svg></span><span class="ratings">1328 Ratings</span></div>
    <p class="card-text">I went out to buy my first car seat and had to earn my PhD in car seats, Newtonian physics, and anti-stain technology…</p>
  </article>

  <!-- Sort -->
  <div class="abs sort">
    <div class="sort-title">Sort by :</div>
    <div class="sort-option">Most recent</div>
    <div class="sort-option">Most popular</div>
    <div class="sort-option">Articles only</div>
    <div class="sort-option">Products only</div>
  </div>

  <!-- More -->
  <div class="abs more-btn">MORE</div>
  <svg class="abs more-chevron" width="28" height="28" viewBox="0 0 28 28" aria-hidden="true">
    <path d="M0 0 H28 V12 L14 26 L0 12 Z" fill="var(--brand-blue)"/>
    <path d="M5 9 L14 18 L23 9" fill="none" stroke="#fff" stroke-width="3"/>
  </svg>

  <footer class="abs footer">Copyright © 2013&nbsp; Company Name | All Rights Reserved</footer>
</body>
</html>
```